I need a website, primarily a landing page, for my company, Morrow Vantage. A sales training and cons

I need a web design/landing page for a new sales training and consulting company, morrow vantage. We perform "sales experiments" aimed at each individual or team, where we assist in helping them identify their strengths, through a series of "sales experiments" that we can tailor based on the individual and what they're trying to accomplish.

```html
<!DOCTYPE html>
<html lang="en">
<head>
<meta charset="utf-8">
<title>Morrow Vantage — Sales Training &amp; Consulting</title>
<link href="https://fonts.googleapis.com/css2?family=Poppins:wght@400;500;600;700&family=Mulish:wght@400;600;700&display=swap" rel="stylesheet">
<style>
:root{
  --blue:#2f78b5;
  --blue-dark:#1d5c93;
  --ink:#222;
  --text:#555;
  --grey:#8a8a8a;
  --black:#000;
  --footer:#2b2b2b;
  --white:#fff;
  --light:#f1f1f1;
}
*{box-sizing:border-box;margin:0;padding:0}
html,body{width:1200px;height:3742px;overflow:hidden;background:var(--white)}
body{position:relative;font-family:"Mulish",Arial,sans-serif;color:var(--text)}
.abs{position:absolute}
h1,h2,h3,h4{font-family:"Poppins",Arial,sans-serif}

/* header */
.topbar{left:0;top:0;width:1200px;height:45px;background:#1c1c1c;color:#fff;font-size:13px}
.topbar .contact{position:absolute;left:724px;top:13px;display:flex;gap:14px;align-items:center}
.topbar .contact span{display:flex;align-items:center;gap:7px}
.header{left:0;top:45px;width:1200px;height:110px;background:var(--white)}
.brand{left:112px;top:0;width:162px;height:155px;background:var(--white);display:flex;align-items:flex-end;justify-content:center;padding-bottom:36px;gap:6px;box-shadow:0 2px 6px rgba(0,0,0,.08)}
.brand .dot{width:12px;height:12px;border-radius:50%;background:var(--blue);margin-bottom:4px}
.brand .name{font-family:"Poppins",sans-serif;font-weight:600;font-size:15px;color:var(--blue);line-height:1.2;text-align:center}
.nav{top:90px;left:0;width:1200px;font-family:"Poppins",sans-serif;font-size:15px;color:#333}
.nav a{position:absolute;color:#333;text-decoration:none}

/* hero */
.hero{left:0;top:155px;width:1200px;height:643px;background:linear-gradient(135deg,#5d6a74 0%,#3b444c 45%,#6f7478 100%)}
.hero .shade{position:absolute;inset:0;background:rgba(0,0,0,.32)}
.hero h1{position:absolute;top:315px;left:0;width:1200px;text-align:center;color:#fff;font-weight:600;font-size:40px}
.hero p{position:absolute;top:382px;left:280px;width:640px;text-align:center;color:#fff;font-size:15px;line-height:26px}
.btn-solid{left:526px;top:454px;width:148px;height:40px;border-radius:20px;background:var(--blue);color:#fff;font-family:"Poppins",sans-serif;font-size:14px;display:flex;align-items:center;justify-content:center}
.arrow{width:44px;height:44px;border-radius:50%;display:flex;align-items:center;justify-content:center}
.hero .arrow.l{left:45px;top:299px;background:#fff}
.hero .arrow.r{left:1108px;top:299px;background:var(--blue)}

/* about */
.about-box{left:112px;top:883px;width:587px;height:359px;border:2px solid #cfcfcf;background:#fff}
.about-box h2{position:absolute;left:33px;top:48px;font-size:36px;font-weight:600;color:var(--blue)}
.about-box p{position:absolute;left:33px;top:108px;width:440px;font-size:14px;line-height:27px;color:var(--text)}
.btn-line{border:2px solid var(--blue);border-radius:20px;color:var(--blue);font-family:"Poppins",sans-serif;font-size:14px;display:flex;align-items:center;justify-content:center}
.about-box .btn-line{position:absolute;left:31px;top:284px;width:144px;height:36px}
.about-photo{left:651px;top:911px;width:434px;height:309px;background:linear-gradient(150deg,#a8b8c4,#5e7282 55%,#2f3d4a);box-shadow:0 10px 24px rgba(0,0,0,.25)}

/* professional band */
.pro{left:0;top:1325px;width:1200px;height:514px;background:linear-gradient(100deg,#1f5f99 0%,#2e6fa8 40%,#3d6a8f 70%,#2b4c6b 100%)}
.pro .eyebrow{position:absolute;left:115px;top:97px;color:#fff;font-family:"Poppins",sans-serif;font-size:17px;font-weight:500}
.pro h2{position:absolute;left:115px;top:130px;color:#fff;font-size:34px;font-weight:600}
.pro p{position:absolute;left:115px;top:190px;width:560px;color:#e8f0f7;font-size:14px;line-height:26px}
.pro .btn-line{position:absolute;left:117px;top:369px;width:142px;height:36px;border-color:#fff;color:#fff}

/* services */
.services h2{position:absolute;left:0;top:1888px;width:1200px;text-align:center;color:var(--blue);font-size:33px;font-weight:600}
.svc-label{font-family:"Poppins",sans-serif;font-size:20px;font-weight:500;transform:translate(-50%,-50%);white-space:nowrap}
.svc-label.on{color:var(--blue)}
.svc-label.off{color:var(--grey)}
.rays{left:376px;top:2150px;width:450px;height:450px;border-radius:50%;background:radial-gradient(circle,#e6e6e6 0%,#efefef 45%,rgba(255,255,255,0) 72%)}
.core{left:514px;top:2288px;width:174px;height:174px;border-radius:50%;background:#ececec}

/* black band */
.established{left:0;top:2612px;width:1200px;height:472px;background:var(--black);color:#fff;text-align:center}
.established .eyebrow{position:absolute;top:90px;left:0;width:1200px;font-family:"Poppins",sans-serif;font-size:17px;font-weight:500}
.established h2{position:absolute;top:140px;left:0;width:1200px;font-size:33px;font-weight:500;line-height:44px}
.established .btn-line{position:absolute;left:524px;top:239px;width:152px;height:40px;border-color:#fff;color:#fff}

/* features card */
.features{left:107px;top:2984px;width:978px;height:339px;background:#fff;box-shadow:0 4px 18px rgba(0,0,0,.14)}
.feature{position:absolute;top:0;width:440px;text-align:center}
.feature .ico{margin:52px auto 0;width:80px;height:80px;border-radius:50%;background:var(--blue);display:flex;align-items:center;justify-content:center}
.feature h3{margin-top:28px;font-size:24px;font-weight:500;color:var(--ink)}
.feature p{margin:14px auto 0;width:380px;font-size:14px;line-height:26px;color:var(--text)}
.features-nav{width:44px;height:44px;border-radius:50%;background:#555;display:flex;align-items:center;justify-content:center}

/* footer */
.footer{left:0;top:3398px;width:1200px;height:344px;background:var(--footer);color:#fff}
.footer h4{position:absolute;top:50px;font-size:17px;font-weight:500}
.footer ul{position:absolute;top:104px;list-style:none;font-size:14px;line-height:27.5px}
.footer .about-text{position:absolute;left:115px;top:104px;width:250px;font-size:13.5px;line-height:25px}
.social{position:absolute;left:115px;top:202px;display:flex;gap:22px}
.social span{width:28px;height:28px;border-radius:50%;background:#fff}
.contact-list{position:absolute;left:886px;top:104px;width:220px;font-size:13px;line-height:20px}
.contact-list div{margin-bottom:14px}
.contact-list b{font-weight:600}
.copy{position:absolute;top:298px;left:0;width:1200px;text-align:center;font-size:14px}
</style>
</head>
<body>

<div class="abs topbar">
  <div class="contact">
    <span><svg width="13" height="13" viewBox="0 0 24 24"><path fill="#fff" d="M6.6 10.8a15 15 0 006.6 6.6l2.2-2.2c.3-.3.7-.4 1-.2 1.1.4 2.3.6 3.6.6.6 0 1 .4 1 1V20c0 .6-.4 1-1 1A17 17 0 013 4c0-.6.4-1 1-1h3.5c.6 0 1 .4 1 1 0 1.3.2 2.5.6 3.6.1.3 0 .7-.2 1z"/></svg>+1 555 - 204 - 7781</span>
    <span>|</span>
    <span><svg width="14" height="11" viewBox="0 0 24 18"><path fill="#fff" d="M0 0h24v18H0z"/><path fill="none" stroke="#1c1c1c" stroke-width="2" d="M1 1l11 9 11-9"/></svg>info@morrowvantage.com</span>
  </div>
</div>
<div class="abs header"></div>
<div class="abs brand"><span class="dot"></span><span class="name">MORROW<br>VANTAGE</span></div>
<nav class="abs nav">
  <a style="left:468px">Home</a>
  <a style="left:547px">About Us</a>
  <a style="left:647px">Services</a>
  <a style="left:745px">Blog</a>
  <a style="left:808px">Testimonials</a>
  <a style="left:935px">Contact Us</a>
  <svg style="position:absolute;left:1046px;top:2px" width="17" height="17" viewBox="0 0 24 24"><circle cx="10" cy="10" r="7" fill="none" stroke="#2f78b5" stroke-width="3"/><path d="M15 15l6 6" stroke="#2f78b5" stroke-width="3"/></svg>
</nav>

<section class="abs hero" role="img" aria-label="Business presenter showing analytics charts to a team seated at a conference table">
  <div class="shade"></div>
  <h1>Optimize Performance in Business &amp; in Life</h1>
  <p>Lorem ipsum dolor sit amet, consectetur adipiscing elit, sed do eiusmod tempor incididunt ut labore et dolore magna aliqua.</p>
  <div class="abs btn-solid">Read More</div>
  <div class="abs arrow l"><svg width="14" height="14" viewBox="0 0 24 24"><path d="M15 4l-8 8 8 8" fill="none" stroke="#333" stroke-width="3"/></svg></div>
  <div class="abs arrow r"><svg width="14" height="14" viewBox="0 0 24 24"><path d="M9 4l8 8-8 8" fill="none" stroke="#fff" stroke-width="3"/></svg></div>
</section>

<section>
  <div class="abs about-box">
    <h2>About Us</h2>
    <p>Lorem ipsum dolor sit amet, consectetur adipiscing elit, sed do eiusmod tempor incididunt ut labore et dolore magna aliqua. Ut enim ad minim veniam, quis nostrud exercitation ullamco laboris nisi ut aliquip ex ea commodo consequat. Duis aute irure dolor in reprehenderit in voluptate velit esse cillum dolore eu fugiat nulla pariatur.</p>
    <div class="btn-line">Read More</div>
  </div>
  <div class="abs about-photo" role="img" aria-label="Consultant presenting a chart on a screen to a seated team in a meeting room"></div>
</section>

<section class="abs pro" role="img" aria-label="Blue-toned world map with silhouettes of business people at a table">
  <div class="eyebrow">Professional Services</div>
  <h2>Training And Consulting Company</h2>
  <p>Sed ut perspiciatis unde omnis iste natus error sit voluptatem accusantium doloremque laudantium, totam rem aperiam, eaque ipsa quae ab illo inventore veritatis et quasi architecto beatae vitae dicta sunt explicabo. Nemo enim ipsam voluptatem quia voluptas sit aspernatur aut odit aut fugit, sed quia consequuntur magni dolores eos qui ratione voluptatem sequi nesciunt.</p>
  <div class="btn-line">Read More</div>
</section>

<section class="services">
  <h2>Morrow Vantage Services</h2>
  <div class="abs rays" role="img" aria-label="Soft grey radiating burst behind the service circle"></div>
  <div class="abs core"></div>
  <svg class="abs" style="left:0;top:1839px" width="1200" height="773" viewBox="0 1839 1200 773">
    <g fill="none" stroke-width="5">
      <circle cx="596" cy="2041" r="50" stroke="#2f78b5"/>
      <circle cx="851" cy="2141" r="50" stroke="#2f78b5"/>
      <circle cx="933" cy="2333" r="50" stroke="#2f78b5"/>
      <circle cx="352" cy="2138" r="50" stroke="#8a8a8a"/>
      <circle cx="249" cy="2330" r="50" stroke="#8a8a8a"/>
    </g>
  </svg>
  <div class="abs svc-label on" style="left:601px;top:1961px">Consulting</div>
  <div class="abs svc-label off" style="left:247px;top:2081px">Strategy</div>
  <div class="abs svc-label on" style="left:980px;top:2093px">Marketing</div>
  <div class="abs svc-label off" style="left:170px;top:2258px">Advisory</div>
  <div class="abs svc-label on" style="left:1040px;top:2275px">Training</div>
</section>

<section class="abs established">
  <div class="eyebrow">Professional Services</div>
  <h2>We are an established business that has<br>been around for over 15 years</h2>
  <div class="btn-line">Contact Us</div>
</section>

<section class="abs features">
  <div class="feature" style="left:40px">
    <div class="ico"><svg width="40" height="40" viewBox="0 0 24 24"><path fill="#fff" d="M3 17h18v2H3zM5 16a7 7 0 0114 0z"/></svg></div>
    <h3>Expert Consultant</h3>
    <p>Donec sed eros fermentum, cursus dui eget, bibendum nibh. Donec scelerisque sollicitudin magna, in viverra lacus placerat quis. Maecenas tincidunt nisl</p>
  </div>
  <div class="feature" style="left:516px">
    <div class="ico"><svg width="40" height="40" viewBox="0 0 24 24"><circle cx="7" cy="7" r="2.5" fill="#fff"/><circle cx="17" cy="7" r="2.5" fill="#fff"/><path fill="#fff" d="M3 20v-6a4 4 0 018 0v6zM13 20v-6a4 4 0 018 0v6z"/></svg></div>
    <h3>Risk Management</h3>
    <p>Donec sed eros fermentum, cursus dui eget, bibendum nibh. Donec scelerisque sollicitudin magna, in viverra lacus placerat quis. Maecenas tincidunt nisl</p>
  </div>
</section>
<div class="abs features-nav" style="left:80px;top:3141px"><svg width="12" height="12" viewBox="0 0 24 24"><path d="M15 4l-8 8 8 8" fill="none" stroke="#fff" stroke-width="3"/></svg></div>
<div class="abs features-nav" style="left:1066px;top:3141px"><svg width="12" height="12" viewBox="0 0 24 24"><path d="M9 4l8 8-8 8" fill="none" stroke="#fff" stroke-width="3"/></svg></div>

<footer class="abs footer">
  <h4 style="left:115px">About Us</h4>
  <p class="about-text">Lorem ipsum dolor sit amet, consectetur adipiscing elit, sed do eiusmod tempor</p>
  <div class="social"><span></span><span></span><span></span><span></span></div>
  <h4 style="left:427px">Quick Links</h4>
  <ul style="left:427px"><li>Home</li><li>About Us</li><li>Services</li><li>Blog</li><li>Testimonials</li><li>Contact Us</li></ul>
  <h4 style="left:638px">Services</h4>
  <ul style="left:638px"><li>Consulting</li><li>Marketing</li><li>Training</li><li>Strategy</li><li>Advisory</li></ul>
  <h4 style="left:883px">Contact Us</h4>
  <div class="contact-list">
    <div><b>Address</b> : #24, Lorem ipsum dolor sit amet Fairhaven</div>
    <div><b>Phone</b> : +1 555 - 204 - 7781</div>
    <div><b>Email</b> : info@morrowvantage.com</div>
  </div>
  <div class="copy">© 2018 Copyrights | All Rights Reserved</div>
</footer>

</body>
</html>
```